Design a compelling Tarnwove Business Card that will drive people to my site

I want a business card that I can give to people—less to tell them who I am and more to direct them to my website. My website is a portal for Pelmor Aquatics Officials and a place for people who want to become Pelmor Aquatics Officials.
I am uploading my official company logo as well as a business card mockup that I did on my own. Please feel free to completely stray from this design.
I've included a screen recording of the homepage of my website as well.
Target Market(s)
Pelmor Aquatics Officials and people who desire to become one
Contact Information for Business Card
website url
Look and feel
Each slider illustrates characteristics of the customer's brand and the style your logo design should communicate.

```html
<!DOCTYPE html>
<html lang="en">
<head>
<meta charset="utf-8">
<title>Tarnwove Business Card</title>
<link href="https://fonts.googleapis.com/css2?family=Poppins:wght@400;600;700&display=swap" rel="stylesheet">
<style>
  :root {
    --brand-blue: #3a53a4;
    --brand-light: #8fa6d9;
    --ink: #3b3b3b;
    --paper: #ffffff;
    --stage: #e9eaee;
  }
  * { margin: 0; padding: 0; box-sizing: border-box; }
  html, body { width: 1200px; height: 900px; overflow: hidden; }
  body {
    background: var(--stage);
    font-family: "Poppins", sans-serif;
    position: relative;
  }
  .card {
    position: absolute;
    left: 250px;
    width: 700px;
    height: 400px;
    box-shadow: 0 10px 30px rgba(0,0,0,0.18);
    overflow: hidden;
  }
  .card--front { top: 40px; background: var(--paper); }
  .card--back { top: 460px; background: var(--brand-blue); }

  /* front */
  .identity {
    position: absolute;
    left: 48px;
    top: 100px;
  }
  .identity__name {
    font-weight: 700;
    font-size: 27px;
    color: var(--brand-blue);
    line-height: 1.1;
  }
  .identity__name span { color: var(--brand-light); }
  .identity__role {
    font-size: 17px;
    color: var(--ink);
    margin-top: 4px;
  }
  .divider {
    position: absolute;
    left: 48px;
    top: 218px;
    width: 604px;
    height: 3px;
    background: linear-gradient(90deg, var(--brand-blue) 0 280px, var(--brand-light) 280px);
  }
  .contact-list {
    position: absolute;
    left: 48px;
    top: 242px;
    list-style: none;
  }
  .contact-list li {
    display: flex;
    align-items: center;
    gap: 10px;
    font-size: 17px;
    color: var(--ink);
    line-height: 1.6;
  }
  .contact-list svg { width: 16px; height: 16px; fill: var(--brand-blue); flex: none; }

  .wordmark {
    position: absolute;
    right: 60px;
    top: 128px;
    font-weight: 600;
    font-size: 60px;
    letter-spacing: -1px;
    color: var(--brand-blue);
    line-height: 1;
  }

  /* back */
  .back__wordmark {
    position: absolute;
    left: 0; right: 0;
    top: 120px;
    text-align: center;
    font-weight: 600;
    font-size: 96px;
    letter-spacing: -2px;
    color: var(--paper);
    line-height: 1;
  }
  .back__band {
    position: absolute;
    left: 0; right: 0;
    top: 262px;
    height: 44px;
    background: linear-gradient(90deg, rgba(143,166,217,0) 10%, rgba(143,166,217,0.55) 50%, rgba(143,166,217,0) 90%);
    display: flex;
    align-items: center;
    justify-content: center;
  }
  .back__tagline {
    font-size: 22px;
    color: var(--paper);
    letter-spacing: 0.5px;
  }
</style>
</head>
<body>
  <section class="card card--front">
    <div class="identity">
      <h1 class="identity__name">Marcus <span>Ellery</span></h1>
      <p class="identity__role">CEO &amp; Founder</p>
    </div>
    <div class="wordmark">tarnwove</div>
    <div class="divider"></div>
    <ul class="contact-list">
      <li><svg viewBox="0 0 16 16"><path d="M3 1h3l1.5 4-2 1.2a9 9 0 0 0 4.3 4.3L11 8.5l4 1.5v3a2 2 0 0 1-2 2A13 13 0 0 1 1 3a2 2 0 0 1 2-2z"/></svg>(555) 014-2273</li>
      <li><svg viewBox="0 0 16 16"><path d="M1 3h14v10H1z M2 4l6 5 6-5" fill="none" stroke="#3a53a4" stroke-width="1.6"/></svg>marcus@tarnwove.com</li>
      <li><svg viewBox="0 0 16 16"><circle cx="8" cy="8" r="7"/></svg>www.tarnwove.com</li>
    </ul>
  </section>

  <section class="card card--back">
    <div class="back__wordmark">tarnwove</div>
    <div class="back__band"><p class="back__tagline">Your Poolside Officiating Hub</p></div>
  </section>
</body>
</html>
```